Local Roofing/Construction company business needs new biz card design

We need a new business card design, current cards are from the start of this operation and generic at best. We are a local Construction Company (General Contractor) with a majority of our work originating from insurance claims-exterior finish work is the main focus (Roofs-Siding-Gutters etc). Heavily involved with homeowners and the low ball offers they receive from insurance company's after a insurable event takes place. I have attached some of our original logo file(s) below.

```html
<!DOCTYPE html>
<html lang="en">
<head>
<meta charset="UTF-8">
<title>Halvard Build Co. — Business Card</title>
<link href="https://fonts.googleapis.com/css2?family=Poppins:wght@300;400;700&display=swap" rel="stylesheet">
<style>
  :root {
    --backdrop: #222324;
    --card-white: #ffffff;
    --card-black: #141516;
    --brand-green: #2fd479;
    --ink: #1e1e1e;
    --rule: #9a9a9a;
  }
  * { margin: 0; padding: 0; box-sizing: border-box; }
  html, body { width: 1200px; height: 1108px; overflow: hidden; }
  body {
    background: var(--backdrop);
    font-family: "Poppins", sans-serif;
    position: relative;
  }
  .card {
    position: absolute;
    top: 254px;
    width: 360px;
    height: 600px;
    border-radius: 22px;
    overflow: hidden;
  }
  .card-front {
    left: 190px;
    background: var(--card-white);
    text-align: center;
    color: var(--ink);
  }
  .card-back {
    left: 650px;
    background: var(--card-black);
  }

  .brand-block {
    margin: 48px auto 0;
    width: 248px;
    height: 210px;
    display: flex;
    flex-direction: column;
    align-items: center;
    justify-content: center;
    gap: 18px;
  }
  .brand-mark {
    width: 54px;
    height: 54px;
    background: var(--brand-green);
    border-radius: 8px;
  }
  .brand-name {
    font-weight: 700;
    font-size: 30px;
    line-height: 1.1;
    color: var(--brand-green);
    letter-spacing: 1px;
    text-transform: uppercase;
  }

  .person-name {
    margin-top: 22px;
    font-weight: 700;
    font-size: 27px;
    line-height: 1.3;
    color: var(--brand-green);
    letter-spacing: 0.5px;
    text-transform: uppercase;
  }
  .person-role {
    font-weight: 400;
    font-size: 15px;
    letter-spacing: 1px;
    text-transform: uppercase;
    margin-top: 2px;
  }

  .icon-row {
    display: flex;
    align-items: center;
    justify-content: center;
    gap: 6px;
    margin: 16px 28px 0;
  }
  .icon-row .rule-line { flex: 1; height: 1px; background: var(--rule); }
  .contact-icon {
    width: 26px;
    height: 26px;
    background: var(--brand-green);
    border-radius: 4px;
    display: flex;
    align-items: center;
    justify-content: center;
  }
  .contact-list {
    list-style: none;
    margin-top: 10px;
    font-size: 17px;
    line-height: 1.45;
    font-weight: 400;
  }
  .divider {
    height: 1px;
    background: var(--rule);
    margin: 12px 40px 12px;
  }
  .address {
    font-size: 15px;
    line-height: 1.5;
    font-weight: 400;
  }

  .back-pattern {
    position: absolute;
    inset: 0;
    background: linear-gradient(200deg, #4a4b4d 0%, #26272a 40%, #111214 75%, #0b0b0c 100%);
  }
  .back-brand {
    position: absolute;
    right: 56px;
    bottom: 150px;
    font-weight: 700;
    font-size: 26px;
    color: var(--brand-green);
    letter-spacing: 1px;
    text-transform: uppercase;
  }
</style>
</head>
<body>
  <section class="card card-front">
    <div class="brand-block">
      <div class="brand-mark"></div>
      <div class="brand-name">Halvard<br>Build Co.</div>
    </div>
    <h1 class="person-name">Marcus Delaney</h1>
    <p class="person-role">Managing Director</p>

    <div class="icon-row">
      <span class="rule-line"></span>
      <span class="contact-icon" aria-label="Phone">
        <svg width="16" height="16" viewBox="0 0 24 24"><path fill="#fff" d="M6.6 10.8a15.1 15.1 0 0 0 6.6 6.6l2.2-2.2c.3-.3.7-.4 1-.2 1.1.4 2.3.6 3.6.6.6 0 1 .4 1 1V20c0 .6-.4 1-1 1A17 17 0 0 1 3 4c0-.6.4-1 1-1h3.5c.6 0 1 .4 1 1 0 1.3.2 2.5.6 3.6.1.3 0 .7-.2 1z"/></svg>
      </span>
      <span class="contact-icon" aria-label="Email">
        <svg width="16" height="16" viewBox="0 0 24 24"><rect x="3" y="5" width="18" height="14" rx="1.5" fill="none" stroke="#fff" stroke-width="2"/><path d="M3.5 6l8.5 7 8.5-7" fill="none" stroke="#fff" stroke-width="2"/></svg>
      </span>
      <span class="contact-icon" aria-label="Website">
        <svg width="16" height="16" viewBox="0 0 24 24"><circle cx="12" cy="12" r="9" fill="none" stroke="#fff" stroke-width="2"/><path d="M3 12h18M12 3c3 3 3 15 0 18M12 3c-3 3-3 15 0 18" fill="none" stroke="#fff" stroke-width="1.6"/></svg>
      </span>
      <span class="rule-line"></span>
    </div>

    <ul class="contact-list">
      <li>055-310 772 418</li>
      <li>hello@halvardbuild.com</li>
      <li>www.halvardbuild.com</li>
    </ul>
    <div class="divider"></div>
    <p class="address">88, Ridgeway Lane North<br>60718, Eastvale</p>
  </section>

  <section class="card card-back">
    <div class="back-pattern" role="img" aria-label="Repeating tone-on-tone brand monogram pattern in glossy black and grey"></div>
    <div class="back-brand">Halvard</div>
  </section>
</body>
</html>
```